Corvanta Group business card redesign

Please throw away what we have and start from scratch. We are bored with our Corvanta Group cards, they need a refresh and as we have introduced a new company to the fold it is the perfect time. Please come up with something that pops. Finishes like foil embossing or engraving are all on the table. Please not be afraid to turn it on it's head. Creative people only.
Target Market(s)
From engineers, to builders, to DIY
Industry/Entity Type
Manufacturer
Contact Information for Business Card
Double sided
Colors
9bcb3c
0255a3
0592cd
Requirements
Must have
- All logos must be shown, the four company logs can be on the back. The group logo is the only one that must be on the front. .
Nice to have
- a design that will age well, we are looking for at least 5 years from the cards.
Should not have
- Please do not send me designs which are just templates that are on the internet, you will be wasting your and my time. As I have searched and searched online and have not found anything I like.

```html
<!DOCTYPE html>
<html lang="en">
<head>
<meta charset="UTF-8">
<title>Corvanta Group – Business Card</title>
<link href="https://fonts.googleapis.com/css2?family=Source+Sans+3:wght@400;600;700&display=swap" rel="stylesheet">
<style>
  :root {
    --stage: #000000;
    --card-white: #ffffff;
    --brand-green: #8cc63f;
    --brand-navy: #1d3f8f;
    --ink: #1f1f1f;
    --rule: #c9c9c9;
  }
  * { margin: 0; padding: 0; box-sizing: border-box; }
  html, body {
    width: 1200px; height: 899px; overflow: hidden;
    background: var(--stage);
    font-family: "Source Sans 3", Arial, sans-serif;
  }
  .stage { position: relative; width: 1200px; height: 899px; }
  .card {
    position: absolute; top: 306px; width: 440px; height: 270px;
    border-radius: 9px; overflow: hidden;
  }
  .card--front { left: 149px; background: var(--card-white); }
  .card--back  { left: 608px; background: var(--brand-green); }

  .wordmark {
    position: absolute; display: flex; align-items: center; gap: 7px;
    font-weight: 700; color: var(--brand-navy); letter-spacing: 0.5px;
    white-space: nowrap; line-height: 1;
  }
  .wordmark__dot { width: 10px; height: 10px; border-radius: 50%; background: var(--brand-navy); flex: none; }
  .card--front .wordmark { left: 34px; width: 196px; top: 129px; font-size: 19px; }
  .card--back .wordmark { left: 0; right: 0; justify-content: center; top: 119px; font-size: 30px; letter-spacing: 1px; }

  .divider { position: absolute; left: 240px; top: 68px; width: 1px; height: 140px; background: var(--rule); }

  .contact { position: absolute; left: 251px; top: 64px; color: var(--ink); }
  .contact__name { font-size: 17px; font-weight: 600; color: var(--brand-navy); line-height: 1.2; }
  .contact__role { font-size: 12.5px; line-height: 1.2; }
  .contact__address { margin-top: 16px; font-size: 12.5px; line-height: 1.15; }
  .contact__list { list-style: none; margin-top: 13px; font-size: 12.5px; }
  .contact__list li { display: flex; align-items: center; gap: 6px; line-height: 18px; }
  .contact__list svg { width: 9px; height: 9px; fill: var(--brand-navy); flex: none; }

  .partner-strip {
    position: absolute; left: 0; top: 203px; width: 100%; height: 52px;
    background: var(--card-white);
    display: flex; align-items: center; justify-content: center; gap: 18px;
  }
  .partner { font-size: 11px; font-weight: 700; color: var(--brand-navy); white-space: nowrap; }
</style>
</head>
<body>
<main class="stage">
  <section class="card card--front">
    <div class="wordmark"><span class="wordmark__dot"></span>CORVANTA GROUP</div>
    <div class="divider"></div>
    <div class="contact">
      <p class="contact__name">Daniel Harper</p>
      <p class="contact__role">Managing Director</p>
      <p class="contact__address">12345, Address Goes Here<br>Country Name, 123456</p>
      <ul class="contact__list">
        <li><svg viewBox="0 0 10 10"><path d="M2 0.5 L3.8 2.6 L2.8 3.6 Q4 6 6.4 7.2 L7.4 6.2 L9.5 8 L8.2 9.5 Q3 8.5 0.5 1.8 Z"/></svg>(044)-456-7890</li>
        <li><svg viewBox="0 0 10 10"><rect x="2.5" y="0.5" width="5" height="3"/><rect x="0.5" y="3.5" width="9" height="4.5"/><rect x="2.5" y="7" width="5" height="2.5"/></svg>123-456-7890</li>
        <li><svg viewBox="0 0 10 10"><path d="M0.5 2 H9.5 V8 H0.5 Z M0.5 2 L5 5.5 L9.5 2" fill="none" stroke="var(--brand-navy)" stroke-width="1.2"/></svg>info@youremail.com</li>
      </ul>
    </div>
  </section>

  <section class="card card--back">
    <div class="wordmark">CORVANTA GROUP</div>
    <div class="partner-strip">
      <span class="partner">Corvanta</span>
      <span class="partner">Keltra Forming</span>
      <span class="partner">Novalite EPS</span>
      <span class="partner">Marlow</span>
    </div>
  </section>
</main>
</body>
</html>
```